KRV Photography Business Card Design

I would like a business card designed in the shape of a camera.
Would like to see various camera designs. Would like to see what the card looks like in different colors. Would like to see which logo looks better on the various camera designs so please show me some with the white logo and some with the black logo. If you need a different file formats please let me know.
Project Deadline Extended Reason: My grandfather passed away and dealing with funeral plans so need to extend deadline. Added Tuesday, March 1, 2016
Project Deadline Extended
Reason: I just got back from out of town. My grandfather's passing was the primary focus for me these past few weeks and the funeral is over so now I will concentrate on picking my business card design. I really appreciate each designer who has taken the time to submit a design. Your effort has not gone unnoticed. I look forward to seeing more amazing designs.
Business
Contact Information for Business Card
Dorine
555-418-2706
https://www.facebook.com/krvphotographyfreelance/
MonaDorine@krv-photography.example

```html
<!DOCTYPE html>
<html lang="en">
<head>
<meta charset="utf-8">
<title>KRV Photography – Business Card</title>
<link rel="stylesheet" href="https://fonts.googleapis.com/css2?family=Open+Sans:wght@400;600;700&display=swap">
<style>
  :root {
    --backdrop: #e6e7e9;
    --card-black: #000000;
    --gold: #c9a13b;
    --white: #ffffff;
  }
  html, body {
    margin: 0;
    padding: 0;
    width: 1200px;
    height: 927px;
    overflow: hidden;
    background: var(--backdrop);
  }
  .card-canvas {
    display: block;
    width: 1200px;
    height: 927px;
  }
  .camera-card { fill: var(--card-black); }
  .brand-mark { fill: var(--gold); }
  .brand-name {
    font-family: "Open Sans", sans-serif;
    font-weight: 400;
    font-size: 42px;
    letter-spacing: 4px;
    fill: var(--gold);
  }
  .divider { stroke: var(--white); stroke-width: 2.5; }
  .holder-name {
    font-family: "Open Sans", sans-serif;
    font-weight: 700;
    font-size: 38px;
    letter-spacing: 2px;
    fill: var(--white);
  }
  .contact-line {
    font-family: "Open Sans", sans-serif;
    font-weight: 400;
    font-size: 23px;
    letter-spacing: 1px;
    fill: var(--white);
  }
  .contact-icon {
    fill: none;
    stroke: var(--white);
    stroke-width: 1.8;
    stroke-linejoin: round;
    stroke-linecap: round;
  }
</style>
</head>
<body>
<svg class="card-canvas" viewBox="0 0 1294 1000" xmlns="http://www.w3.org/2000/svg" aria-label="KRV Photography business card shaped like a camera">
  <defs>
    <filter id="card-shadow" x="-10%" y="-10%" width="120%" height="125%">
      <feDropShadow dx="6" dy="8" stdDeviation="8" flood-color="#000" flood-opacity="0.3"/>
    </filter>
  </defs>

  <path class="camera-card" filter="url(#card-shadow)" d="
    M 183 887
    Q 148 887 148 852
    L 148 330
    Q 148 298 185 292
    Q 225 285 265 284
    L 265 262
    Q 266 244 290 242
    L 440 240
    Q 456 242 460 268
    Q 520 262 575 240
    Q 600 228 606 195
    L 612 160
    Q 618 138 648 134
    L 702 127
    L 710 115 L 734 115 L 736 124
    L 845 124
    L 849 113 L 870 113 L 876 128
    L 932 134
    Q 958 140 964 170
    L 970 200
    Q 980 245 1030 262
    L 1110 292
    Q 1146 305 1146 340
    L 1146 852
    Q 1146 887 1111 887
    Z"/>

  <g class="brand">
    <circle class="brand-mark" cx="424" cy="410" r="72"/>
    <text class="brand-name" x="194" y="548">KRV PHOTOGRAPHY</text>
  </g>

  <line class="divider" x1="148" y1="744" x2="770" y2="744"/>

  <g class="contact-block">
    <text class="holder-name" x="1097" y="759" text-anchor="end">THEO MARLOW</text>
    <text class="contact-line" x="1064" y="807" text-anchor="end">+330 5550-1942</text>
    <path class="contact-icon" d="M1084 789 l4 -1 l3 6 l-2 2 q2 4 5 6 l2 -2 l5 3 l-1 4 q-6 2 -12 -6 q-6 -7 -4 -12 Z"/>
    <text class="contact-line" x="1064" y="836" text-anchor="end">theo@marlowmail.example</text>
    <rect class="contact-icon" x="1079" y="822" width="20" height="13" rx="1.5"/>
    <path class="contact-icon" d="M1080 824 l9 7 l9 -7"/>
  </g>
</svg>
</body>
</html>
```